Company web site

Looking for a full responsive(mobile friendly) wordpress implementation

Some material is in the website -- brelvanto.wordpress.com

But looking for a template more consistent with the logo design, and more future looking.

Target Market(s)

Enterprise Clients

Industry/Entity Type

It Company

Font styles to use
Sans Serif

Colors
33a6d7
0255a3
0455a3
cfdeed
85abd2
3176b5

Requirements
Must have
• about, contact information, partner page, success stories, customer testimonials. links to social presence.
• pricing information

```html
<!DOCTYPE html>
<html lang="en">
<head>
<meta charset="utf-8">
<title>Brelvanto — Bridging connected devices with enterprise solutions</title>
<link rel="stylesheet" href="https://fonts.googleapis.com/css2?family=Open+Sans:ital,wght@0,300;0,400;0,600;0,700;1,300;1,400&display=swap">
<style>
:root{
  --sky:#33a6d7;
  --navy:#0255a3;
  --royal:#0455a3;
  --ice:#cfdeed;
  --steel:#85abd2;
  --mid:#3176b5;
  --ink:#333a40;
  --text:#6b7177;
  --muted:#9aa1a7;
  --line:#e4e8ec;
  --footer:#1e1f21;
  --white:#ffffff;
}
*{box-sizing:border-box;margin:0;padding:0}
html,body{width:1200px;height:3224px;overflow:hidden}
body{font-family:"Open Sans",Arial,sans-serif;color:var(--text);background:var(--white);position:relative}
.section{position:absolute;left:0;width:1200px}

/* Navigation */
.site-nav{top:0;height:80px;background:var(--white);display:flex;align-items:center;justify-content:space-between;padding:0 28px 0 44px;box-shadow:0 1px 4px rgba(0,0,0,.08);z-index:2}
.brand{display:flex;align-items:center;gap:10px}
.brand-dot{width:26px;height:26px;border-radius:50%;background:var(--sky)}
.brand-name{font-size:28px;font-weight:600;color:var(--mid);letter-spacing:-.3px}
.menu{display:flex;height:80px;list-style:none}
.menu li{display:flex;align-items:center;padding:0 13px;font-size:13px;font-weight:600;color:var(--ink);letter-spacing:.3px}
.menu li.active{background:var(--sky);color:var(--white);padding:0 20px}

/* Hero */
.hero{top:80px;height:608px;background:linear-gradient(180deg,#a9bfcf 0%,#7c93a6 45%,#4f6474 100%);display:flex;flex-direction:column;align-items:center;justify-content:center;color:var(--white)}
.hero-mark{width:96px;height:96px;border:4px solid var(--white);border-radius:50%;margin-top:40px}
.hero-title{font-size:52px;font-weight:400;letter-spacing:3px;margin-top:18px;text-shadow:0 1px 6px rgba(0,0,0,.25)}
.hero-sub{font-size:22px;font-weight:300;margin-top:4px;text-shadow:0 1px 6px rgba(0,0,0,.3)}

/* Welcome */
.welcome{top:688px;height:624px}
.welcome-screen{position:absolute;left:100px;top:120px;width:244px;height:250px;border-radius:6px;background:linear-gradient(180deg,#2b2f33 0%,#2b2f33 68%,#d5d9dd 68%,#eef0f2 100%)}
.welcome-copy{position:absolute;left:372px;top:136px;width:740px}
.welcome-copy h2{font-size:30px;font-weight:600;color:var(--ink);letter-spacing:.5px;margin-bottom:14px}
.welcome-copy p{font-size:15px;line-height:1.6;color:var(--text)}
.btn-outline{display:inline-block;margin-top:26px;padding:7px 18px;border:1.5px solid var(--mid);border-radius:3px;font-size:12px;color:var(--mid);font-weight:600}

/* Connected */
.connected{top:1312px;height:432px;background:linear-gradient(120deg,#6d86c9 0%,#7c97d3 40%,#5d8fd0 75%,#4c7fc4 100%);color:var(--white)}
.connected h2{position:absolute;top:38px;left:0;width:100%;text-align:center;font-size:24px;font-weight:600;letter-spacing:1px}
.feature{position:absolute;width:470px;display:flex;gap:20px}
.feature-icon{flex:none;width:52px;height:52px;border-radius:50%;background:rgba(255,255,255,.9);display:flex;align-items:center;justify-content:center}
.feature h3{font-size:15px;font-weight:600;letter-spacing:.5px;margin:4px 0 6px}
.feature p{font-size:12.5px;line-height:1.55;color:rgba(255,255,255,.88)}
.feature .more{font-size:12px;margin-top:6px;font-weight:600}
.dots{position:absolute;display:flex;gap:8px}
.dots span{width:9px;height:9px;border-radius:50%;background:rgba(255,255,255,.45)}
.dots span.on{background:var(--white)}

/* Lifecycle */
.lifecycle{top:1744px;height:568px}
.lifecycle h2{position:absolute;top:130px;left:0;width:100%;text-align:center;font-size:30px;font-weight:600;color:var(--ink);line-height:1.3;letter-spacing:.5px}
.stage{position:absolute;width:300px;display:flex;gap:18px}
.stage-icon{flex:none;width:48px;height:48px;border-radius:50%;border:2px solid var(--steel);display:flex;align-items:center;justify-content:center}
.stage h3{font-size:17px;font-weight:600;color:var(--ink);margin-bottom:4px}
.stage p{font-size:12.5px;line-height:1.5;color:var(--muted)}

/* Testimonial */
.testimonial{top:2312px;height:296px;background:linear-gradient(100deg,#4b7dbf 0%,#6b98d2 55%,#86b0e0 100%);color:var(--white)}
.client-photo{position:absolute;left:128px;top:80px;width:136px;height:136px;border-radius:50%;border:4px solid rgba(255,255,255,.85);background:linear-gradient(180deg,#c9d2db 0%,#6f7d8c 100%)}
.quote-badge{position:absolute;left:118px;top:68px;width:40px;height:40px;border-radius:50%;background:var(--sky);display:flex;align-items:center;justify-content:center;font-size:30px;font-weight:700;line-height:1;padding-top:12px}
.testimonial blockquote{position:absolute;left:300px;top:82px;width:780px;font-size:15px;font-style:italic;font-weight:300;line-height:1.65}
.testimonial cite{position:absolute;left:300px;top:206px;font-style:normal;font-size:14px;line-height:1.5}
.testimonial cite b{font-weight:600;display:block}
.arrow{position:absolute;top:128px}

/* Success stories */
.success{top:2608px;height:440px}
.success-copy{position:absolute;left:150px;top:130px;width:560px}
.success-copy h2{font-size:30px;font-weight:600;color:var(--ink);letter-spacing:.5px;margin-bottom:14px}
.success-copy p{font-size:13.5px;line-height:1.6}
.story-photo{position:absolute;left:812px;top:64px;width:312px;height:312px;border-radius:50%;border:6px solid var(--ice);background:linear-gradient(160deg,#dfe6ee 0%,#9fb2c6 55%,#6f7f90 100%)}
.vdots{position:absolute;left:1148px;top:190px;display:flex;flex-direction:column;gap:10px}
.vdots span{width:9px;height:9px;border-radius:50%;background:#c9ced3}
.vdots span.on{background:var(--ink)}

/* Footer */
.site-footer{top:3048px;height:176px;background:var(--footer);color:#c8ccd0;text-align:center}
.footer-links{display:flex;justify-content:center;gap:14px;margin-top:44px;font-size:12px;font-weight:600;letter-spacing:.5px}
.footer-links i{font-style:normal;color:#6c7075}
.social{display:flex;justify-content:center;gap:12px;margin-top:16px}
.social span{width:26px;height:26px;border-radius:50%;border:1.5px solid #8c9095}
.copyright{font-size:11px;margin-top:16px;color:#8c9095}
.page-num{position:absolute;right:30px;bottom:18px;font-size:12px;color:#8c9095}
</style>
</head>
<body>

<header class="section site-nav">
  <div class="brand"><span class="brand-dot"></span><span class="brand-name">Brelvanto</span></div>
  <ul class="menu">
    <li class="active">HOME</li><li>ABOUT</li><li>PARTNERS</li><li>PRICING</li><li>SUCCESS STORIES</li><li>TESTIMONIALS</li><li>CONTACT US</li>
  </ul>
</header>

<section class="section hero" role="img" aria-label="Photo of a team working together at a laptop in a bright office">
  <div class="hero-mark"></div>
  <h1 class="hero-title">BRELVANTO</h1>
  <p class="hero-sub">Bridging connected devices with enterprise solutions</p>
</section>

<section class="section welcome">
  <div class="welcome-screen" role="img" aria-label="Desktop monitor showing the device dashboard with a map"></div>
  <div class="welcome-copy">
    <h2>WELCOME TO BRELVANTO</h2>
    <p>Founded in 2016 by industry veterans, Brelvanto is geared to provide integrated solutions for the IoT industry. With a off-shore development center in Eastern Europe, Brelvanto is positioned to provide extensive development capabilities to our customers. Brelvanto is a company which provides specialized offerings in IoT domain. Based in the heart of the Silicon Valley, California, Brelvanto is built on decades of experience and knowledge.</p>
    <span class="btn-outline">Read More ›</span>
  </div>
</section>

<section class="section connected" role="img" aria-label="Blue tinted photo of connected devices in use">
  <h2>BRELVANTO CONNECTED</h2>

  <div class="feature" style="left:80px;top:108px">
    <div class="feature-icon"><svg width="22" height="22" viewBox="0 0 24 24" fill="none" stroke="#3176b5" stroke-width="2"><circle cx="12" cy="8" r="4"/><path d="M4 21c1-4 4-6 8-6s7 2 8 6"/></svg></div>
    <div><h3>USER MANAGEMENT</h3><p>With Brelvanto you can add and manage users for every customer, assign roles to each team and keep access rules clear across your whole device fleet.</p><div class="more">Read More ›</div></div>
  </div>
  <div class="feature" style="left:640px;top:108px">
    <div class="feature-icon"><svg width="22" height="22" viewBox="0 0 24 24" fill="none" stroke="#3176b5" stroke-width="2"><rect x="3" y="4" width="18" height="12" rx="1"/><path d="M8 20h8M12 16v4"/></svg></div>
    <div><h3>DEVICE MANAGEMENT</h3><p>With Brelvanto you can register, update and monitor every device from one place, push new firmware safely and see the health of each unit at a glance.</p><div class="more">Read More ›</div></div>
  </div>
  <div class="feature" style="left:80px;top:238px">
    <div class="feature-icon"><svg width="22" height="22" viewBox="0 0 24 24" fill="none" stroke="#3176b5" stroke-width="2"><path d="M12 3l8 3v6c0 5-4 8-8 9-4-1-8-4-8-9V6z"/></svg></div>
    <div><h3>SECURITY</h3><p>With Brelvanto every connection is encrypted end to end, keys are rotated for you and each device proves who it is before any data is sent.</p><div class="more">Read More ›</div></div>
  </div>
  <div class="feature" style="left:640px;top:238px">
    <div class="feature-icon"><svg width="22" height="22" viewBox="0 0 24 24" fill="none" stroke="#3176b5" stroke-width="2"><path d="M4 20V10M10 20V4M16 20v-8M22 20H2"/></svg></div>
    <div><h3>ANALYTICS</h3><p>With Brelvanto you can turn device data into clear reports, spot trends early and share live dashboards with the people who need them.</p><div class="more">Read More ›</div></div>
  </div>

  <div class="dots" style="left:578px;top:398px"><span></span><span class="on"></span><span></span></div>
</section>

<section class="section lifecycle">
  <h2>BRELVANTO ENSURES END-TO-END<br>PRODUCT LIFECYCLE MANAGEMENT</h2>

  <div class="stage" style="left:110px;top:280px">
    <div class="stage-icon"><svg width="22" height="22" viewBox="0 0 24 24" fill="none" stroke="#3176b5" stroke-width="2"><circle cx="12" cy="12" r="3"/><path d="M12 2v4M12 18v4M2 12h4M18 12h4M5 5l3 3M16 16l3 3M5 19l3-3M16 8l3-3"/></svg></div>
    <div><h3>Manufacture</h3><p>Secure manufacturing process, device traceability to ERP</p></div>
  </div>
  <div class="stage" style="left:460px;top:280px">
    <div class="stage-icon"><svg width="22" height="22" viewBox="0 0 24 24" fill="none" stroke="#3176b5" stroke-width="2"><path d="M3 4h3l3 11h10l2-8H7"/><circle cx="10" cy="19" r="1.5"/><circle cx="17" cy="19" r="1.5"/></svg></div>
    <div><h3>Sell</h3><p>Sold-out tracking in CRM, access details for customer orders</p></div>
  </div>
  <div class="stage" style="left:810px;top:280px">
    <div class="stage-icon"><svg width="22" height="22" viewBox="0 0 24 24" fill="none" stroke="#3176b5" stroke-width="2"><path d="M5 12l5 5L20 7"/></svg></div>
    <div><h3>Provision</h3><p>Simplify consumer experience during device activation</p></div>
  </div>
  <div class="stage" style="left:110px;top:400px">
    <div class="stage-icon"><svg width="22" height="22" viewBox="0 0 24 24" fill="none" stroke="#3176b5" stroke-width="2"><rect x="7" y="2" width="10" height="20" rx="2"/><path d="M11 18h2"/></svg></div>
    <div><h3>Use</h3><p>Consumer web portal and mobile apps, notifications, social identity</p></div>
  </div>
  <div class="stage" style="left:460px;top:400px">
    <div class="stage-icon"><svg width="22" height="22" viewBox="0 0 24 24" fill="none" stroke="#3176b5" stroke-width="2"><path d="M4 14v-2a8 8 0 0116 0v2"/><rect x="3" y="14" width="4" height="6" rx="1"/><rect x="17" y="14" width="4" height="6" rx="1"/></svg></div>
    <div><h3>Support</h3><p>In-app help, ticketing system and call center integration</p></div>
  </div>
  <div class="stage" style="left:810px;top:400px">
    <div class="stage-icon"><svg width="22" height="22" viewBox="0 0 24 24" fill="none" stroke="#3176b5" stroke-width="2"><path d="M3 17l6-6 4 4 8-8M15 7h6v6"/></svg></div>
    <div><h3>Monetize</h3><p>Recurrent user billing, additional services and payment</p></div>
  </div>
</section>

<section class="section testimonial">
  <svg class="arrow" style="left:64px" width="20" height="36" viewBox="0 0 20 36" fill="none" stroke="#ffffff" stroke-width="2"><path d="M16 4L4 18l12 14"/></svg>
  <div class="client-photo" role="img" aria-label="Portrait photo of the client"></div>
  <div class="quote-badge">“</div>
  <blockquote>It has survived not only five centuries, but also the leap into electronic typesetting, remaining essentially unchanged. It was popularised in the 1960s with the release of sheets containing sample passages, and more recently with desktop publishing software that includes versions of sample text. It has survived not only five centuries, but also the leap into electronic typesetting.</blockquote>
  <cite><b>Tomas Reyvik</b>Founder, Brelvanto</cite>
  <svg class="arrow" style="left:1116px" width="20" height="36" viewBox="0 0 20 36" fill="none" stroke="#ffffff" stroke-width="2"><path d="M4 4l12 14L4 32"/></svg>
</section>

<section class="section success">
  <div class="success-copy">
    <h2>SUCCESS STORIES</h2>
    <p>It is a long established fact that a reader will be distracted by the readable content of a page when looking at its layout. The point of using sample text is that it has a more-or-less normal distribution of letters, as opposed to using plain repeated words, making it look like readable English. Many desktop publishing packages and web page editors now use sample text as their default model text, and a search will uncover many web sites still in their infancy.</p>
    <span class="btn-outline">Read More ›</span>
  </div>
  <div class="story-photo" role="img" aria-label="Circular photo of a customer working at a laptop"></div>
  <div class="vdots"><span class="on"></span><span></span><span></span><span></span></div>
</section>

<footer class="section site-footer">
  <div class="footer-links"><span>ABOUT</span><i>|</i><span>PRIVACY</span><i>|</i><span>TERMS</span><i>|</i><span>LEGAL</span><i>|</i><span>CONTACT</span></div>
  <div class="social"><span></span><span></span><span></span><span></span><span></span><span></span></div>
  <p class="copyright">Copyright © 2017 Brelvanto · All Rights Reserved</p>
  <span class="page-num">1/2</span>
</footer>

</body>
</html>
```